Small Business Broker Business Card Design

A business card design for a small business brokerage, which is a financial service, not unlike real estate brokerage, but for small businesses such as laundromats, pizza shops, restaurants, cleaners etc. The designs should all be simple, more conservative in nature, using the colors and font of the logo. Again, think real estate Brokerage as a business context
Contact Information for Business Card
Name: Glen R. Harlow. Title: Small Business Advisor. Email: g.harlow@bayfieldcapitalworks.example. Mobile: (555) 274-3918. Office: (555) 806-2147. www.bayfieldcapitalworks.example

```html
<!DOCTYPE html>
<html lang="en">
<head>
<meta charset="utf-8">
<title>Bayfield Capital Works – Business Card</title>
<link rel="stylesheet" href="https://fonts.googleapis.com/css2?family=Montserrat:wght@600;700&family=Open+Sans:wght@400;600&display=swap">
<style>
  :root {
    --navy: #1d3f7c;
    --navy-deep: #163363;
    --green: #7cc242;
    --ink: #2e2e33;
    --paper: #ffffff;
    --stage: #2a2c30;
    --rule: #9aa6bd;
  }
  * { box-sizing: border-box; margin: 0; padding: 0; }
  html, body { width: 1200px; height: 900px; overflow: hidden; }
  body {
    background: var(--stage);
    display: flex;
    align-items: center;
    justify-content: center;
    gap: 50px;
    font-family: "Open Sans", Arial, sans-serif;
  }
  .card {
    position: relative;
    width: 525px;
    height: 300px;
    border-radius: 22px;
    overflow: hidden;
  }
  .card-art { position: absolute; inset: 0; width: 100%; height: 100%; }

  /* Front */
  .card--front { background: var(--paper); }
  .brand {
    position: absolute;
    left: 28px;
    top: 66px;
    width: 222px;
  }
  .brand-row { display: flex; align-items: center; gap: 6px; }
  .brand-square { width: 10px; height: 10px; background: var(--navy); flex: none; }
  .brand-name {
    font-family: "Montserrat", Arial, sans-serif;
    font-weight: 700;
    font-size: 11.5px;
    letter-spacing: 0.3px;
    color: var(--navy);
    text-transform: uppercase;
    white-space: nowrap;
    line-height: 1.2;
  }
  .brand-tagline {
    margin-top: 5px;
    padding-left: 16px;
    font-family: "Montserrat", Arial, sans-serif;
    font-weight: 600;
    font-size: 6.5px;
    letter-spacing: 0.5px;
    color: var(--green);
    text-transform: uppercase;
    white-space: nowrap;
  }
  .divider {
    position: absolute;
    left: 262px;
    top: 48px;
    width: 1px;
    height: 150px;
    background: var(--rule);
  }
  .contact {
    position: absolute;
    left: 280px;
    top: 46px;
    color: var(--ink);
  }
  .contact-name {
    font-family: "Montserrat", Arial, sans-serif;
    font-weight: 700;
    font-size: 19px;
    color: var(--navy);
    text-transform: uppercase;
    letter-spacing: 0.3px;
  }
  .contact-name .surname { color: var(--green); }
  .contact-title { font-size: 11px; margin-top: 2px; }
  .contact-address { font-size: 10.5px; margin-top: 8px; line-height: 1.45; }
  .contact-list { list-style: none; margin-top: 8px; font-size: 10.5px; line-height: 1.6; }
  .contact-list li { display: flex; align-items: center; gap: 6px; white-space: nowrap; }
  .icon { width: 10px; height: 10px; flex: none; fill: var(--navy); }

  /* Back */
  .card--back { background: var(--navy); }
  .back-brand {
    position: absolute;
    inset: 0;
    display: flex;
    flex-direction: column;
    align-items: center;
    justify-content: center;
    gap: 10px;
  }
  .back-name {
    font-family: "Montserrat", Arial, sans-serif;
    font-weight: 700;
    font-size: 24px;
    letter-spacing: 1px;
    color: var(--paper);
    text-transform: uppercase;
    white-space: nowrap;
  }
  .back-tagline {
    font-family: "Montserrat", Arial, sans-serif;
    font-weight: 600;
    font-size: 10px;
    letter-spacing: 1.2px;
    color: var(--green);
    text-transform: uppercase;
    white-space: nowrap;
  }
</style>
</head>
<body>

<section class="card card--front" aria-label="Business card front">
  <svg class="card-art" viewBox="0 0 525 300" preserveAspectRatio="none" aria-hidden="true">
    <path d="M0 150 C 90 215, 260 285, 440 300 L0 300 Z" fill="var(--navy)"/>
    <path d="M0 132 C 90 205, 260 280, 450 300" fill="none" stroke="var(--green)" stroke-width="3"/>
  </svg>

  <div class="brand">
    <div class="brand-row">
      <span class="brand-square"></span>
      <span class="brand-name">Bayfield Capital Works, Inc</span>
    </div>
    <p class="brand-tagline">Trusted guidance for every main street sale</p>
  </div>

  <div class="divider"></div>

  <div class="contact">
    <h1 class="contact-name">Glen R. <span class="surname">Harlow</span></h1>
    <p class="contact-title">Small Business Advisor</p>
    <p class="contact-address">P.O. Box 418 Harbor Lane<br>Bayfield ON, K2B 5R1</p>
    <ul class="contact-list">
      <li>
        <svg class="icon" viewBox="0 0 10 10"><path d="M2 0.5 L3.6 0.5 L4.2 3 L3 3.8 C3.6 5 4.8 6.3 6.2 7 L7 5.8 L9.5 6.4 L9.5 8 C9.5 9 8.8 9.5 8 9.5 C4 9.2 0.8 6 0.5 2 C0.5 1.2 1 0.5 2 0.5 Z"/></svg>
        (555) 274-3918
      </li>
      <li>
        <svg class="icon" viewBox="0 0 10 10"><rect x="2.2" y="0.5" width="5.6" height="9" rx="1"/><rect x="3" y="1.5" width="4" height="6" fill="var(--paper)"/></svg>
        (555) 806-2147
      </li>
      <li>
        <svg class="icon" viewBox="0 0 10 10"><rect x="0.5" y="2" width="9" height="6.5" rx="0.8"/><path d="M0.8 2.4 L5 5.6 L9.2 2.4" fill="none" stroke="var(--paper)" stroke-width="0.9"/></svg>
        g.harlow@bayfieldcapitalworks.example
      </li>
      <li>
        <svg class="icon" viewBox="0 0 10 10"><circle cx="5" cy="5" r="4.5"/><path d="M0.5 5 H9.5 M5 0.5 C3 3, 3 7, 5 9.5 M5 0.5 C7 3, 7 7, 5 9.5" fill="none" stroke="var(--paper)" stroke-width="0.7"/></svg>
        www.bayfieldcapitalworks.example
      </li>
    </ul>
  </div>
</section>

<section class="card card--back" aria-label="Business card back">
  <svg class="card-art" viewBox="0 0 525 300" preserveAspectRatio="none" aria-hidden="true">
    <path d="M60 0 L200 0 L525 230 L525 300 L470 300 L60 0 Z" fill="#ffffff" opacity="0.05"/>
    <path d="M260 0 L340 0 L525 130 L525 190 Z" fill="#ffffff" opacity="0.05"/>
    <path d="M0 120 L0 60 L330 300 L250 300 Z" fill="var(--navy-deep)" opacity="0.6"/>
  </svg>
  <div class="back-brand">
    <p class="back-name">Bayfield Capital Works, Inc</p>
    <p class="back-tagline">Trusted guidance for every main street sale</p>
  </div>
</section>

</body>
</html>
```